Brivolt Technologies business card design

We need a business card designed with our new logo. it would be great if the card could communicate it is a technology based company.

Target Market(s)

system integrators

Industry/Entity Type

technology, IOT

Contact Information for Business Card

Name, designation, Address, telephone number, email address

Requirements
Must have
• logo and company name
Nice to have
• something to do with technology

```html
<!DOCTYPE html>
<html lang="en">
<head>
<meta charset="utf-8">
<title>Brivolt Technologies – Business Card</title>
<link href="https://fonts.googleapis.com/css2?family=Arimo:wght@400;700&display=swap" rel="stylesheet">
<style>
  :root {
    --backdrop: #d9d9da;
    --card: #1f1f21;
    --card-edge: #c8660e;
    --orange: #ef7f1a;
    --white: #f4f4f4;
    --emboss: #3c3c40;
  }
  * { margin: 0; padding: 0; box-sizing: border-box; }
  html, body { width: 1200px; height: 800px; overflow: hidden; }
  body {
    background: var(--backdrop);
    font-family: "Arimo", Arial, sans-serif;
    position: relative;
  }
  .card {
    position: absolute;
    width: 520px;
    height: 300px;
    background: var(--card);
    border-radius: 18px;
    border-bottom: 3px solid var(--card-edge);
    overflow: hidden;
  }
  .card--front { left: 70px; top: 90px; }
  .card--back { left: 610px; top: 410px; }

  /* Front: brand block in the lower-left */
  .brand-mark {
    position: absolute;
    left: 34px;
    bottom: 34px;
    display: flex;
    align-items: center;
    gap: 16px;
  }
  .brand-mark__square {
    width: 96px;
    height: 96px;
    background: var(--orange);
    flex: none;
  }
  .brand-mark__name {
    font-weight: 700;
    font-size: 24px;
    line-height: 1.15;
    color: var(--white);
  }

  /* Front: contact column in the upper-right */
  .front-info {
    position: absolute;
    right: 34px;
    top: 28px;
    text-align: right;
    color: var(--white);
  }
  .company-name {
    font-weight: 700;
    font-size: 20px;
    letter-spacing: 1px;
    line-height: 1.1;
    color: var(--white);
    margin-bottom: 18px;
  }
  .person-name {
    font-weight: 700;
    font-size: 18px;
    color: var(--orange);
  }
  .person-role {
    font-size: 12px;
    margin-bottom: 14px;
  }
  .address { font-size: 12px; line-height: 1.4; margin-bottom: 12px; }
  .contacts { list-style: none; font-size: 12px; line-height: 1.45; }
  .contacts li { display: flex; justify-content: flex-end; align-items: center; gap: 8px; }
  .contacts svg { width: 11px; height: 11px; }

  /* Back: embossed brand centred */
  .back-brand {
    position: absolute;
    inset: 0;
    display: flex;
    align-items: center;
    justify-content: center;
    gap: 16px;
  }
  .back-brand__square {
    width: 52px;
    height: 52px;
    background: var(--emboss);
  }
  .back-brand__name {
    font-weight: 700;
    font-size: 30px;
    letter-spacing: 1px;
    color: var(--emboss);
  }
</style>
</head>
<body>
  <section class="card card--front">
    <div class="brand-mark">
      <span class="brand-mark__square" aria-hidden="true"></span>
      <p class="brand-mark__name">Brivolt<br>Technologies</p>
    </div>

    <div class="front-info">
      <p class="company-name">Brivolt Technologies</p>
      <p class="person-name">Daniel Moreno</p>
      <p class="person-role">Managing Director</p>
      <p class="address">4120 Linden Court<br>Fairbanks, Alaska 99701</p>
      <ul class="contacts">
        <li>555-214-7830
          <svg viewBox="0 0 12 12" aria-hidden="true"><path d="M3 1 L5 3.5 L4 5 Q5.5 7.5 7 8 L8.5 7 L11 9 L9.5 11 Q4 10 1 3 Z" fill="var(--orange)"/></svg></li>
        <li>555-290-1146
          <svg viewBox="0 0 12 12" aria-hidden="true"><rect x="3" y="0.5" width="6" height="11" rx="1" fill="none" stroke="var(--white)" stroke-width="1.2"/></svg></li>
        <li>info@brivolt.com
          <svg viewBox="0 0 12 12" aria-hidden="true"><rect x="0.5" y="2" width="11" height="8" fill="var(--orange)"/><path d="M0.5 2 L6 7 L11.5 2" fill="none" stroke="var(--card)" stroke-width="1"/></svg></li>
        <li>www.brivolt.com
          <svg viewBox="0 0 12 12" aria-hidden="true"><circle cx="6" cy="6" r="5.5" fill="var(--orange)"/><path d="M0.5 6 H11.5 M6 0.5 V11.5" stroke="var(--card)" stroke-width="0.9"/></svg></li>
      </ul>
    </div>
  </section>

  <section class="card card--back">
    <div class="back-brand">
      <span class="back-brand__square" aria-hidden="true"></span>
      <p class="back-brand__name">Brivolt Technologies</p>
    </div>
  </section>
</body>
</html>
```